Corvane Freight Company Business Card Design

We are a company that delivers natural saltwater (from the ocean) to aquarium companies, restaurants and home marine tanks. I would like a new business card to suit.

Must include Name, company name, abn, contact number and website as well as logo (see attached).

Looking for a design that stands out, has a clean but unique appearance.

Double and single sided entries welcome

Business

• Logo

```html
<!DOCTYPE html>
<html lang="en">
<head>
<meta charset="utf-8">
<title>Corvane Freight Company – Business Card</title>
<link rel="stylesheet" href="https://fonts.googleapis.com/css2?family=Source+Sans+3:wght@400;600;700&display=swap">
<style>
  :root {
    --stage: #2a2a2a;
    --card-blue: #1763f0;
    --band-blue: #3db2f4;
    --white: #ffffff;
    --text-soft: #e8f0ff;
  }
  * { box-sizing: border-box; margin: 0; padding: 0; }
  html, body { width: 1200px; height: 1114px; overflow: hidden; }
  body {
    background: var(--stage);
    position: relative;
    font-family: "Source Sans 3", "Helvetica Neue", Arial, sans-serif;
    color: var(--white);
  }
  .card {
    position: absolute;
    width: 768px;
    height: 437px;
    background: var(--card-blue);
    overflow: hidden;
  }
  .card--front { left: 77px; top: 98px; }
  .card--back  { left: 349px; top: 591px; }

  .brand-name {
    position: absolute;
    left: 0; right: 0;
    text-align: center;
    font-weight: 700;
    font-size: 64px;
    letter-spacing: -0.5px;
    line-height: 1;
    color: var(--white);
  }
  .card--front .brand-name { top: 92px; }
  .card--back  .brand-name { top: 166px; }

  .contact {
    position: absolute;
    top: 278px;
    font-size: 19px;
    line-height: 27px;
    color: var(--text-soft);
  }
  .contact--address { right: 366px; text-align: right; }
  .contact--lines { left: 420px; }
  .contact--lines li { list-style: none; display: flex; align-items: center; gap: 6px; }
  .contact-divider {
    position: absolute;
    left: 402px; top: 278px;
    width: 1px; height: 82px;
    background: var(--text-soft);
  }
  .contact-icon { width: 15px; height: 15px; flex: none; }

  .rule {
    position: absolute;
    left: 0; right: 0; top: 380px;
    height: 3px;
    background: var(--band-blue);
  }
  .name-band {
    position: absolute;
    left: 0; right: 0; top: 389px; bottom: 0;
    background: var(--band-blue);
    display: flex; align-items: center; justify-content: center;
    font-size: 23px;
  }
  .name-band strong { font-weight: 700; margin-right: 6px; }
  .name-band span { font-weight: 400; }

  .web-address {
    position: absolute;
    left: 0; right: 0; top: 351px;
    text-align: center;
    font-size: 23px;
    letter-spacing: 3.5px;
    color: var(--text-soft);
  }
</style>
</head>
<body>
  <section class="card card--front" aria-label="Business card front">
    <div class="brand-name">Corvane Freight</div>

    <address class="contact contact--address" style="font-style:normal">
      Corvane Freight Company<br>
      Street Name, City Name<br>
      State, City Zip Code
    </address>
    <div class="contact-divider"></div>
    <ul class="contact contact--lines">
      <li>
        <svg class="contact-icon" viewBox="0 0 16 16" aria-hidden="true">
          <path fill="none" stroke="#e8f0ff" stroke-width="1.6" d="M4 2l2.5 3-1.5 2a8 8 0 0 0 4 4l2-1.5 3 2.5-1.5 2C7 14 2 9 2 3.5z"/>
        </svg>
        123-456-7890
      </li>
      <li>
        <svg class="contact-icon" viewBox="0 0 16 16" aria-hidden="true">
          <circle cx="8" cy="8" r="6" fill="#e8f0ff"/>
        </svg>
        www.website.com
      </li>
      <li>ABN : 0123456789</li>
    </ul>

    <div class="rule"></div>
    <div class="name-band"><strong>Your name,</strong><span>Title</span></div>
  </section>

  <section class="card card--back" aria-label="Business card back">
    <div class="brand-name">Corvane Freight</div>
    <div class="web-address">www.website.com</div>
  </section>
</body>
</html>
```